Brell Stone Company Business Cards

Front and Back Business Card - logo and text setup - cool design. I need workable photoshop or illustrator files so I can setup each employee card with design that is created
Updates

Hi everyone, thank you for the great entries. Please no more white and blue cards - there are so many already - black and silver only now please. thanks!

Target Market(s)

Construction Industry - Facility Managers

Industry/Entity Type

Construction

Contact Information for Business Card

I really like contemporary simplistic looks - clean neat....not opposed to seeing some black backrounds

Requirements
Must have
• Logo/website address with design on front only - www.brellstone-example.com (logo attached)
• Back:
• Name/Title/Company Address/Phone/email address
Nice to have
• Cool design
Should not have
• Nothing gimmicky like Fire or Water - since we are a Fire Protection company - it has all been done

```html
<!DOCTYPE html>
<html lang="en">
<head>
<meta charset="utf-8">
<title>Brell Stone Company – Business Cards</title>
<link href="https://fonts.googleapis.com/css2?family=Lato:wght@400;700;900&display=swap" rel="stylesheet">
<style>
  :root {
    --backdrop: #7b4a1f;
    --card: #000000;
    --silver-bright: #c9c9c9;
    --silver: #a4a4a4;
    --silver-dim: #8c8c8c;
    --rule: #4a4a4a;
  }
  * { margin: 0; padding: 0; box-sizing: border-box; }
  html, body {
    width: 1200px;
    height: 900px;
    overflow: hidden;
    background: var(--backdrop);
    font-family: "Lato", sans-serif;
  }
  .card {
    position: absolute;
    background: var(--card);
    box-shadow: 3px 4px 8px rgba(0, 0, 0, 0.45);
    text-align: center;
  }
  .card--details { left: 330px; top: 90px; width: 555px; height: 345px; }
  .card--brand { left: 330px; top: 469px; width: 559px; height: 344px; }

  .contact-block {
    position: absolute;
    left: 0; right: 0; top: 72px;
    display: flex;
    flex-direction: column;
    align-items: center;
  }
  .person-name {
    font-size: 21px;
    font-weight: 700;
    letter-spacing: 0.3px;
    color: var(--silver-bright);
    line-height: 26px;
  }
  .person-title {
    font-size: 16px;
    color: var(--silver);
    line-height: 20px;
  }
  .divider {
    width: 196px;
    height: 1px;
    background: var(--rule);
    margin: 10px 0 8px;
  }
  .contact-lines, .address {
    font-size: 16px;
    line-height: 20px;
    color: var(--silver-dim);
  }
  .contact-lines .label { color: var(--silver-bright); }

  .brand-name {
    position: absolute;
    left: 0; right: 0; top: 138px;
    font-size: 40px;
    font-weight: 900;
    color: var(--silver-bright);
    display: flex;
    justify-content: center;
    align-items: center;
    gap: 14px;
  }
  .brand-mark {
    width: 18px;
    height: 18px;
    background: var(--silver-bright);
  }
  .brand-url {
    position: absolute;
    left: 0; right: 0; top: 284px;
    font-size: 16px;
    color: var(--silver);
  }
</style>
</head>
<body>
  <section class="card card--details">
    <div class="contact-block">
      <p class="person-name">DANIEL PORTER</p>
      <p class="person-title">Managing Director</p>
      <div class="divider"></div>
      <p class="contact-lines"><span class="label">P:</span> 044-987 654 321</p>
      <p class="contact-lines"><span class="label">E:</span> hello@brellstone-example.com</p>
      <p class="contact-lines"><span class="label">W:</span> www.brellstone-example.com</p>
      <div class="divider"></div>
      <p class="address">12345, Address Goes Here</p>
      <p class="address">Country Name, 123456.</p>
    </div>
  </section>

  <section class="card card--brand">
    <div class="brand-name"><span class="brand-mark"></span>Brell Stone Company</div>
    <p class="brand-url">www.brellstone-example.com</p>
  </section>
</body>
</html>
```